Locksmith Business Cards

My father-in-law is in need of new business cards for his locksmith business and I need to impress him. Kindly help me out!

You can see the previous business card attached. It is a family run business in North Wales.

No individual names on the cards.

Key Things to Feature:
- The words "Prompt", "Local", "Reliable" (as you can see under the logo on the website)
- 24h Emergency Service
- Covering All of North Wales, the Wirral and Chester
- The color blue
- A key or a lock would be interesting (similar to the ones that come up when you google locksmith business card)

Optional (only if design includes bullet points, like the example below):
https://imgvaultcdn.net/samples/208314/55172/55172_3904821_208314_image.jpg
- Residential / Commercial / Automotive
- Alarms & Cameras
- Key Cutting & Safes

https://www.brynhafod-locksmiths.co.uk/

Industry/Entity Type

Locksmith

Contact Information for Business Card

01632 960 418
07700 900 362
brynhafodlocksmiths@mailvane.com
Brynhafod Locksmiths, The Willow Barn, 7 Tannery Rd., Llandudno LL99 4QX
www.brynhafod-locksmiths.co.uk

Requirements
Must have
• - The words "Prompt", "Local", "Reliable" (as you can see under the logo on the website)
• - 24h Emergency Service
• - Covering All of North Wales, the Wirral and Chester
Nice to have
• - A key or a lock would be interesting (similar to the ones that come up when you google locksmith business card)

```html
<!DOCTYPE html>
<html lang="en">
<head>
<meta charset="utf-8">
<title>Brynhafod Locksmiths – Business Cards</title>
<link rel="stylesheet" href="https://fonts.googleapis.com/css2?family=Oswald:wght@500&family=Roboto:wght@300;400&display=swap">
<style>
  :root {
    --backdrop: #3a3a3a;
    --navy-deep: #1c205a;
    --navy: #262b6b;
    --blue-mid: #3f4c9a;
    --blue-light: #6a7fc4;
    --stripe: #4557a8;
    --white: #ffffff;
    --ink: #232862;
  }
  * { margin: 0; padding: 0; box-sizing: border-box; }
  html, body { width: 1200px; height: 900px; overflow: hidden; }
  body {
    background: var(--backdrop);
    font-family: "Roboto", Arial, sans-serif;
    position: relative;
  }
  .card {
    position: absolute;
    width: 700px;
    height: 400px;
    overflow: hidden;
    box-shadow: 0 10px 30px rgba(0,0,0,0.45);
  }

  /* Front */
  .card-front {
    left: 400px; top: 50px;
    background: linear-gradient(100deg, var(--navy-deep) 0%, var(--navy) 40%, var(--blue-light) 100%);
    color: var(--white);
  }
  .front-wordmark {
    position: absolute;
    left: 0; right: 0; top: 92px;
    text-align: center;
    font-family: "Oswald", "Arial Narrow", sans-serif;
    font-weight: 500;
    font-size: 46px;
    line-height: 1;
    letter-spacing: 1px;
    text-transform: uppercase;
    color: var(--white);
  }
  .front-tagline {
    position: absolute;
    left: 0; right: 0; top: 208px;
    text-align: center;
    font-size: 17px;
    font-weight: 300;
    line-height: 1.3;
    letter-spacing: 0.5px;
  }

  /* Back */
  .card-back {
    left: 130px; top: 475px;
    background: var(--white);
  }
  .back-wave { position: absolute; inset: 0; }
  .back-wordmark {
    position: absolute;
    left: 60px; top: 40px;
    font-family: "Oswald", "Arial Narrow", sans-serif;
    font-weight: 500;
    font-size: 38px;
    line-height: 1.05;
    letter-spacing: 1px;
    text-transform: uppercase;
    color: var(--ink);
  }
  .address {
    position: absolute;
    right: 40px; top: 142px;
    text-align: right;
    font-size: 18px;
    line-height: 1.4;
    color: var(--ink);
  }
  .services {
    position: absolute;
    left: 36px; top: 238px;
    list-style: none;
    color: var(--white);
    font-size: 19px;
    line-height: 1.55;
  }
  .services li { display: flex; align-items: center; gap: 8px; }
  .services svg { width: 28px; height: 14px; flex: none; }
  .contacts {
    position: absolute;
    right: 28px; top: 268px;
    list-style: none;
    color: var(--white);
    font-size: 19px;
    line-height: 1.45;
    text-align: right;
  }
  .contacts li { display: flex; justify-content: flex-end; align-items: center; gap: 10px; }
  .contacts svg { width: 18px; height: 18px; flex: none; }
</style>
</head>
<body>

<section class="card card-front" aria-label="Business card front">
  <h1 class="front-wordmark">Brynhafod<br>Locksmiths</h1>
  <p class="front-tagline">
    PROMPT - LOCAL - RELIABLE<br>
    24h Emergency Service<br>
    Covering All of North Wales, the Wirral and Chester
  </p>
</section>

<section class="card card-back" aria-label="Business card back">
  <svg class="back-wave" viewBox="0 0 700 400" preserveAspectRatio="none" aria-hidden="true">
    <defs>
      <linearGradient id="waveFill" x1="0" y1="0" x2="1" y2="0.3">
        <stop offset="0" stop-color="#1c205a"/>
        <stop offset="0.5" stop-color="#3a4694"/>
        <stop offset="1" stop-color="#6a7fc4"/>
      </linearGradient>
    </defs>
    <path d="M0,190 C140,150 280,160 400,212 C500,252 600,258 700,238 L700,400 L0,400 Z" fill="url(#waveFill)"/>
    <path d="M350,192 C450,232 560,242 700,222 L700,230 C560,252 450,242 350,192 Z" fill="var(--stripe)"/>
  </svg>

  <h2 class="back-wordmark">Brynhafod<br>Locksmiths</h2>

  <p class="address">The Willow Barn, 7 Tannery Rd.<br>Llandudno LL99 4QX</p>

  <ul class="services">
    <li><svg viewBox="0 0 28 14" aria-hidden="true"><circle cx="6" cy="7" r="4.5" fill="none" stroke="#fff" stroke-width="1.5"/><path d="M10.5 7H27M20 7v4M24 7v3" stroke="#fff" stroke-width="1.5" fill="none"/></svg>Residential</li>
    <li><svg viewBox="0 0 28 14" aria-hidden="true"><circle cx="6" cy="7" r="4.5" fill="none" stroke="#fff" stroke-width="1.5"/><path d="M10.5 7H27M20 7v4M24 7v3" stroke="#fff" stroke-width="1.5" fill="none"/></svg>Commercial</li>
    <li><svg viewBox="0 0 28 14" aria-hidden="true"><circle cx="6" cy="7" r="4.5" fill="none" stroke="#fff" stroke-width="1.5"/><path d="M10.5 7H27M20 7v4M24 7v3" stroke="#fff" stroke-width="1.5" fill="none"/></svg>Automotive</li>
    <li><svg viewBox="0 0 28 14" aria-hidden="true"><circle cx="6" cy="7" r="4.5" fill="none" stroke="#fff" stroke-width="1.5"/><path d="M10.5 7H27M20 7v4M24 7v3" stroke="#fff" stroke-width="1.5" fill="none"/></svg>Alarms &amp; Cameras</li>
    <li><svg viewBox="0 0 28 14" aria-hidden="true"><circle cx="6" cy="7" r="4.5" fill="none" stroke="#fff" stroke-width="1.5"/><path d="M10.5 7H27M20 7v4M24 7v3" stroke="#fff" stroke-width="1.5" fill="none"/></svg>Key Cutting &amp; Safes</li>
  </ul>

  <ul class="contacts">
    <li>01632 960 418<svg viewBox="0 0 18 18" aria-hidden="true"><path d="M2 6c0-2 2-3 7-3s7 1 7 3v1h-3V5.5H5V7H2z" fill="#fff"/><path d="M4 8h10l1 7H3z" fill="#fff"/></svg></li>
    <li>07700 900 362<svg viewBox="0 0 18 18" aria-hidden="true"><path d="M2 6c0-2 2-3 7-3s7 1 7 3v1h-3V5.5H5V7H2z" fill="#fff"/><path d="M4 8h10l1 7H3z" fill="#fff"/></svg></li>
    <li>brynhafodlocksmiths@mailvane.com<svg viewBox="0 0 18 18" aria-hidden="true"><rect x="1" y="4" width="16" height="11" fill="#fff"/><path d="M1 4l8 6 8-6" fill="none" stroke="#3f4c9a" stroke-width="1.4"/></svg></li>
    <li>www.brynhafod-locksmiths.co.uk<svg viewBox="0 0 18 18" aria-hidden="true"><circle cx="9" cy="9" r="7.5" fill="none" stroke="#fff" stroke-width="1.5"/><ellipse cx="9" cy="9" rx="3" ry="7.5" fill="none" stroke="#fff" stroke-width="1.2"/><path d="M1.5 9h15" stroke="#fff" stroke-width="1.2"/></svg></li>
  </ul>
</section>

</body>
</html>
```